TA BRAMLEY BUSINESS CARD DESIGN PROJECT

We need to utilize our logo that was expertly created on PixelHarbor and now need to match this with a business card design.

```html
<!DOCTYPE html>
<html lang="en">
<head>
<meta charset="utf-8">
<title>TA BRAMLEY Business Card</title>
<link href="https://fonts.googleapis.com/css2?family=Montserrat:wght@400;500;700;800&display=swap" rel="stylesheet">
<style>
  :root {
    --brand-blue: #0f57ab;
    --card-white: #ffffff;
    --ink-dark: #2a2a2a;
    --card-black: #171717;
    --emboss-grey: #2c2c2c;
    --stage: #e4e4e2;
  }
  * { box-sizing: border-box; margin: 0; padding: 0; }
  html, body { width: 1200px; height: 801px; overflow: hidden; }
  body {
    background: var(--stage);
    font-family: "Montserrat", sans-serif;
    position: relative;
  }
  .card {
    position: absolute;
    top: 250px;
    width: 525px;
    height: 300px;
    overflow: hidden;
    box-shadow: 0 6px 18px rgba(0,0,0,0.18);
  }
  .card-front { left: 50px; background: var(--card-white); }
  .card-back { left: 625px; background: var(--card-black); }

  .front-sweep { position: absolute; inset: 0; }

  .name-tab {
    position: absolute;
    top: 22px; right: 0;
    width: 16px; height: 38px;
    background: var(--brand-blue);
  }
  .person {
    position: absolute;
    top: 22px; right: 28px;
    text-align: right;
  }
  .person-name {
    font-weight: 800;
    font-size: 19px;
    color: var(--brand-blue);
    letter-spacing: 0.5px;
  }
  .person-role {
    font-size: 12px;
    color: var(--ink-dark);
    margin-top: 2px;
  }

  .brand-name {
    position: absolute;
    left: 28px; top: 34px;
    font-weight: 800;
    font-size: 22px;
    color: var(--brand-blue);
    letter-spacing: 3px;
    display: flex; align-items: center; gap: 8px;
  }
  .brand-name .brand-dot {
    width: 12px; height: 12px; background: var(--brand-blue);
  }
  .brand-feature {
    position: absolute;
    right: 28px; top: 80px;
    font-weight: 800;
    font-size: 30px;
    line-height: 1;
    color: var(--brand-blue);
    letter-spacing: 2px;
    white-space: nowrap;
  }

  .contact {
    position: absolute;
    left: 28px; top: 98px;
    font-size: 12px;
    color: var(--ink-dark);
    line-height: 1.5;
  }
  .contact-address { margin-bottom: 10px; }
  .contact-list { list-style: none; }
  .contact-list li { display: flex; align-items: center; gap: 7px; }
  .contact-list svg { width: 11px; height: 11px; fill: var(--brand-blue); flex: none; }

  .back-brand {
    position: absolute;
    inset: 0;
    display: flex; align-items: center; justify-content: center;
    font-weight: 800;
    font-size: 46px;
    letter-spacing: 8px;
    color: var(--emboss-grey);
  }
</style>
</head>
<body>

  <section class="card card-front" aria-label="Card front">
    <svg class="front-sweep" viewBox="0 0 525 300" preserveAspectRatio="none">
      <path d="M0 300 L0 285 C200 275 400 220 525 130 L525 300 Z" fill="var(--brand-blue)"/>
      <path d="M110 300 C260 285 420 235 525 165" fill="none" stroke="var(--card-white)" stroke-width="5"/>
    </svg>

    <div class="name-tab"></div>
    <div class="person">
      <p class="person-name">MARCUS ELLERY</p>
      <p class="person-role">Managing Director</p>
    </div>

    <div class="brand-name"><span class="brand-dot"></span>TA BRAMLEY</div>
    <div class="brand-feature">TA BRAMLEY</div>

    <div class="contact">
      <p class="contact-address">Your address, City<br>State, Zip 1234</p>
      <ul class="contact-list">
        <li><svg viewBox="0 0 12 12"><path d="M2 1h3l1 3-1.5 1a6 6 0 0 0 2.5 2.5L8 6l3 1v3a1 1 0 0 1-1 1A9 9 0 0 1 1 2a1 1 0 0 1 1-1z"/></svg>123 456 789</li>
        <li><svg viewBox="0 0 12 12"><rect x="2" y="1" width="8" height="10" rx="1"/></svg>123 456 789</li>
        <li><svg viewBox="0 0 12 12"><path d="M1 3h10v6H1z"/><path d="M1 3l5 4 5-4" fill="none" stroke="#fff" stroke-width="1"/></svg>info@tabramley.com</li>
        <li><svg viewBox="0 0 12 12"><circle cx="6" cy="6" r="5"/></svg>www.tabramley.com</li>
      </ul>
    </div>
  </section>

  <section class="card card-back" aria-label="Card back">
    <div class="back-brand">TA BRAMLEY</div>
  </section>

</body>
</html>
```